Redesign of business card for Cedar Ridge Mechanical

We are looking for a new design for our business cards for Cedar Ridge Mechanical. We are a plumbing & HVAC construction company, operating on the West Coast of Canada and USA. Logo attached.
Industry/Entity Type
Construction - Plumbing & HVAC
Contact Information for Business Card
Name, address, phone numbers, email, website address
Look and feel
Each slider illustrates characteristics of the customer's brand and the style your logo design should communicate.

```html
<!DOCTYPE html>
<html lang="en">
<head>
<meta charset="utf-8">
<title>Cedar Ridge Mechanical – Business Card</title>
<link rel="stylesheet" href="https://fonts.googleapis.com/css2?family=Oswald:wght@600&family=Roboto:wght@400;700&display=swap">
<style>
  :root {
    --backdrop: #c9c9c9;
    --card-white: #ffffff;
    --card-dark: #2b2b2b;
    --ink: #111111;
    --ink-soft: #555555;
    --ink-muted: #8a8a8a;
    --rule: #b5b5b5;
    --band: #000000;
    --back-text: #e6e6e6;
    --back-mark: #4a4a4a;
  }
  * { margin: 0; padding: 0; box-sizing: border-box; }
  html, body { width: 1200px; height: 800px; overflow: hidden; }
  body {
    background: var(--backdrop);
    font-family: "Roboto", Arial, sans-serif;
    position: relative;
  }
  .card {
    position: absolute;
    top: 250px;
    width: 520px;
    height: 300px;
    border-radius: 22px;
    overflow: hidden;
  }
  /* Front */
  .card--front { left: 60px; background: var(--card-white); }
  .card--front .edge-band {
    position: absolute; left: 0; right: 0; bottom: 0; height: 12px;
    background: var(--band);
  }
  .brand {
    position: absolute; left: 40px; top: 52px;
    display: flex; align-items: center; gap: 14px;
  }
  .brand__square {
    width: 40px; height: 40px; background: var(--ink);
  }
  .brand__name {
    font-family: "Oswald", "Arial Narrow", sans-serif;
    font-weight: 600; font-size: 26px; letter-spacing: 1px;
    text-transform: uppercase; color: var(--ink);
  }
  .details {
    position: absolute; left: 40px; right: 32px; bottom: 42px;
    display: flex; align-items: flex-end;
  }
  .person { width: 240px; }
  .person__name { font-weight: 700; font-size: 20px; color: var(--ink); }
  .person__title { font-size: 14px; color: var(--ink-muted); margin-top: 2px; }
  .person__address { font-size: 14px; color: var(--ink-soft); margin-top: 14px; line-height: 1.35; }
  .divider { width: 1px; height: 88px; background: var(--rule); margin: 0 20px; }
  .contact { list-style: none; font-size: 14px; color: var(--ink-soft); }
  .contact li { display: flex; align-items: center; gap: 8px; line-height: 1.5; }
  .contact svg { width: 11px; height: 11px; fill: var(--ink); flex: none; }
  /* Back */
  .card--back { left: 620px; background: var(--card-dark); }
  .back-brand {
    position: absolute; left: 0; right: 0; top: 96px;
    display: flex; justify-content: center; align-items: center; gap: 16px;
  }
  .back-brand__square { width: 46px; height: 46px; background: var(--back-mark); }
  .back-brand__name {
    font-family: "Oswald", "Arial Narrow", sans-serif;
    font-weight: 600; font-size: 30px; letter-spacing: 1px;
    text-transform: uppercase; color: var(--back-mark);
  }
  .website {
    position: absolute; left: 0; right: 0; bottom: 44px;
    text-align: center; font-size: 16px; color: var(--back-text); letter-spacing: .3px;
  }
</style>
</head>
<body>
  <section class="card card--front" aria-label="Card front">
    <div class="brand">
      <span class="brand__square"></span>
      <span class="brand__name">Cedar Ridge Mechanical</span>
    </div>
    <div class="details">
      <div class="person">
        <p class="person__name">Daniel Marsh</p>
        <p class="person__title">President</p>
        <p class="person__address">2170 Harbour View Road<br>Port Alder, BC V0R 2K0</p>
      </div>
      <span class="divider"></span>
      <ul class="contact">
        <li><svg viewBox="0 0 24 24" aria-hidden="true"><path d="M6.6 10.8a15.1 15.1 0 0 0 6.6 6.6l2.2-2.2c.3-.3.7-.4 1-.2 1.1.4 2.3.6 3.6.6.6 0 1 .4 1 1V20c0 .6-.4 1-1 1A17 17 0 0 1 3 4c0-.6.4-1 1-1h3.5c.6 0 1 .4 1 1 0 1.3.2 2.5.6 3.6.1.3 0 .7-.2 1z"/></svg>(604) 555-0182</li>
        <li><svg viewBox="0 0 24 24" aria-hidden="true"><path d="M2 5h20v14H2z M2 5l10 8 10-8" /></svg>name@cedarridgemechanical.com</li>
      </ul>
    </div>
    <span class="edge-band"></span>
  </section>

  <section class="card card--back" aria-label="Card back">
    <div class="back-brand">
      <span class="back-brand__square"></span>
      <span class="back-brand__name">Cedar Ridge Mechanical</span>
    </div>
    <p class="website">www.cedarridgemechanical.com</p>
  </section>
</body>
</html>
```